Dunmore Roofing

Want a professional looking business card

Industry/Entity Type

Business

Contact Information for Business Card

Paul Dunmore ( Owner) paul@dunmoreroofing-example.com, www.dunmoreroofing-example.com, Adress: 4172 Township road 43 Plantagenet,ON K9X4T2

```html
<!DOCTYPE html>
<html lang="en">
<head>
<meta charset="utf-8">
<title>Dunmore Roofing — Business Card</title>
<link rel="stylesheet" href="https://fonts.googleapis.com/css2?family=Roboto:wght@400;500&family=Roboto+Condensed:wght@500;700&display=swap">
<style>
  :root {
    --brand-blue: #1e4a8e;
    --brand-grey: #7d7d7d;
    --ink: #404040;
    --rule: #a9a9a9;
    --paper: #f7f7f6;
    --backdrop: #e9e6e1;
  }
  * { box-sizing: border-box; margin: 0; padding: 0; }
  html, body { width: 1200px; height: 960px; overflow: hidden; }
  body {
    background: var(--backdrop);
    font-family: "Roboto", Arial, sans-serif;
    color: var(--ink);
    position: relative;
  }
  .card {
    position: absolute;
    width: 600px;
    height: 343px;
    background: var(--paper);
    box-shadow: 0 2px 6px rgba(0,0,0,0.25);
  }
  .card--front { left: 314px; top: 123px; }
  .card--back  { left: 311px; top: 482px; }

  .front-band {
    position: absolute; left: 0; right: 0; bottom: 0; height: 17px;
    background: var(--brand-blue);
    border-top: 3px solid #c9c9c9;
  }

  .wordmark {
    position: absolute;
    font-family: "Roboto Condensed", Arial, sans-serif;
    font-weight: 700;
    color: var(--brand-blue);
    text-transform: uppercase;
    line-height: 1;
    display: flex;
    align-items: center;
    gap: 12px;
  }
  .wordmark__square { width: 14px; height: 14px; background: var(--brand-blue); flex: none; }
  .wordmark__lines { display: flex; flex-direction: column; }
  .wordmark--front { right: 26px; top: 108px; font-size: 30px; letter-spacing: 5px; }
  .wordmark--front .wordmark__lines { align-items: flex-end; margin-right: -5px; }
  .wordmark--front .wordmark__sub { font-size: 14px; letter-spacing: 21px; margin-right: -16px; margin-top: 6px; }
  .wordmark--back { left: 0; right: 0; top: 184px; justify-content: center; font-size: 38px; letter-spacing: 7px; }
  .wordmark--back .wordmark__lines { align-items: center; margin-right: -7px; }
  .wordmark--back .wordmark__sub { font-size: 17px; letter-spacing: 27px; margin-right: -20px; margin-top: 8px; }

  .holder { position: absolute; left: 27px; top: 194px; right: 27px; }
  .holder__name {
    font-family: "Roboto Condensed", Arial, sans-serif;
    font-weight: 500;
    font-size: 23px;
    color: var(--brand-blue);
    text-transform: uppercase;
    line-height: 1;
  }
  .holder__role {
    display: flex; align-items: center; gap: 4px;
    margin-top: 6px;
    font-size: 14px; color: var(--brand-grey); text-transform: uppercase; letter-spacing: 0.3px;
  }
  .holder__role::after { content: ""; flex: 1; height: 1px; background: var(--rule); }

  .contacts { position: absolute; left: 27px; top: 247px; list-style: none; font-size: 14px; line-height: 19px; }
  .contacts li { display: flex; align-items: center; gap: 8px; }
  .contacts svg { width: 13px; height: 13px; fill: var(--brand-blue); flex: none; }

  .address { position: absolute; right: 25px; top: 266px; text-align: right; font-size: 14px; line-height: 19px; font-style: normal; }

  .back-url {
    position: absolute; left: 0; right: 0; top: 285px;
    text-align: center; font-size: 13px; letter-spacing: 5px; color: var(--ink);
  }
</style>
</head>
<body>
  <section class="card card--front" aria-label="Business card front">
    <div class="wordmark wordmark--front">
      <span class="wordmark__square"></span>
      <span class="wordmark__lines"><span>Dunmore</span><span class="wordmark__sub">Roofing</span></span>
    </div>

    <div class="holder">
      <h1 class="holder__name">Paul Dunmore</h1>
      <p class="holder__role">Owner</p>
    </div>

    <ul class="contacts">
      <li>
        <svg viewBox="0 0 16 16" aria-hidden="true"><path d="M3.2 1.2l2.3 0 1.2 3.4-1.6 1.2c.9 1.9 2.3 3.3 4.2 4.2l1.2-1.6 3.4 1.2 0 2.3c0 1-.8 1.8-1.8 1.8C6.4 13.7 2.3 9.6 1.4 3c0-1 .8-1.8 1.8-1.8z"/></svg>
        613 555 0187
      </li>
      <li>
        <svg viewBox="0 0 16 16" aria-hidden="true"><path d="M1 3h14v10H1z M2.5 4.5L8 8.6l5.5-4.1z" fill-rule="evenodd"/></svg>
        paul@dunmoreroofing-example.com
      </li>
      <li>
        <svg viewBox="0 0 16 16" aria-hidden="true"><circle cx="8" cy="8" r="7"/><path d="M4 5c1.5 0 2.5 1 2 2.5S4 9 4.5 11M9 2.5c0 2 2 2 3 3.5s-1 3 0 5" stroke="#f7f7f6" stroke-width="1.3" fill="none"/></svg>
        www.dunmoreroofing-example.com
      </li>
    </ul>

    <address class="address">4172 Township road 43<br>Harrowfield, ON K9X4T2</address>

    <div class="front-band"></div>
  </section>

  <section class="card card--back" aria-label="Business card back">
    <div class="wordmark wordmark--back">
      <span class="wordmark__square"></span>
      <span class="wordmark__lines"><span>Dunmore</span><span class="wordmark__sub">Roofing</span></span>
    </div>
    <p class="back-url">www.dunmoreroofing-example.com</p>
  </section>
</body>
</html>
```